Business card design needed

Our company background is that we provides transfers to and from the airport, social & corporate events, weddings.
We are also available for charter for birthday party, wine tastings, concerts, anniversary, school balls etc.
Our business cards have to reflect that we have a professional company, they are our first contact and have to stand out from the other 'players' in the market.

Industry/Entity Type

School

Contact Information for Business Card

TELVIK BDR, Lorcan & Mirabel, mob: 0428 351 972, PO Box 847, Brellin VR 6971, ABN 52 714 309 268, Lic 7164/2918,

Requirements
Must have
• Telephone number: 0428 351 972
Website: www.TELVIKBDR.com.au
postal address: PO Box 847, Brellin VR 6971
Licences: Lic 7164/2918

***If using the new photo (one with the bus and buildings behind it), if possible can the buildings be cropped out. Thanks
Nice to have
• would be nice to have the pics of the vehicle(s), preferred the Vorn on the card but not too fussed.
Should not have
• Picture of vehicle we don't have in our fleet. (We ONLY have the Vornelles and Korimu Daltra mini bus)

```html
<!DOCTYPE html>
<html lang="en">
<head>
<meta charset="utf-8">
<title>TELVIK BDR — Business Card</title>
<link rel="stylesheet" href="https://fonts.googleapis.com/css2?family=Open+Sans:wght@300;400&display=swap">
<style>
  :root {
    --ink-black: #000000;
    --panel-light: #3c3f41;
    --panel-mid: #1c1e1f;
    --band: #0b0b0b;
    --text: #f2f2f2;
    --rule: #e6e6e6;
    --vehicle-light: #e9ecee;
    --vehicle-shade: #8a9096;
  }
  html, body {
    margin: 0;
    padding: 0;
    width: 1200px;
    height: 741px;
    overflow: hidden;
    background: var(--ink-black);
  }
  .card {
    position: relative;
    width: 1200px;
    height: 741px;
    background: var(--ink-black);
    font-family: "Open Sans", Arial, sans-serif;
    color: var(--text);
    overflow: hidden;
  }
  .contact-panel {
    position: absolute;
    left: 0; top: 0;
    width: 430px;
    height: 694px;
    background: linear-gradient(100deg, var(--panel-light) 0%, var(--panel-mid) 55%, #0d0e0e 100%);
  }
  .bottom-band {
    position: absolute;
    left: 0; bottom: 0;
    width: 1200px;
    height: 47px;
    background: var(--band);
  }
  .brand {
    position: absolute;
    left: 760px;
    top: 68px;
    width: 370px;
    border-top: 2px solid var(--rule);
  }
  .brand-primary {
    display: block;
    text-align: right;
    font-weight: 300;
    font-size: 90px;
    line-height: 1;
    letter-spacing: 2px;
    margin-top: 11px;
    padding-right: 8px;
  }
  .brand-secondary {
    display: block;
    text-align: right;
    font-weight: 300;
    font-size: 45px;
    line-height: 1;
    letter-spacing: 4px;
    margin-top: 13px;
    padding-right: 8px;
  }
  .names {
    position: absolute;
    left: 47px;
    top: 280px;
    margin: 0;
    font-weight: 400;
    font-size: 31px;
    letter-spacing: 1px;
  }
  .names-rule {
    position: absolute;
    left: 49px;
    top: 343px;
    width: 334px;
    height: 2px;
    background: var(--rule);
  }
  .details {
    position: absolute;
    left: 49px;
    top: 385px;
    margin: 0;
    padding: 0;
    list-style: none;
    font-size: 19.5px;
    line-height: 1;
  }
  .details li {
    position: absolute;
    left: 0;
    white-space: nowrap;
  }
  .details .mobile  { top: 2px; }
  .details .postal  { top: 51px; }
  .details .abn     { top: 108px; }
  .details .licence { top: 157px; }
  .details .web     { top: 206px; }
  .vehicle-photo {
    position: absolute;
    left: 592px;
    top: 290px;
    width: 540px;
    height: 372px;
    border-radius: 90px 50px 40px 60px;
    background: radial-gradient(ellipse at 45% 45%, var(--vehicle-light) 0%, #c9cdd1 45%, var(--vehicle-shade) 75%, rgba(0,0,0,0) 100%);
  }
</style>
</head>
<body>
  <div class="card">
    <div class="contact-panel"></div>
    <div class="bottom-band"></div>

    <div class="brand">
      <span class="brand-primary">TELVIK</span>
      <span class="brand-secondary">BDR</span>
    </div>

    <h1 class="names">LORCAN &amp; MIRABEL</h1>
    <div class="names-rule"></div>

    <ul class="details">
      <li class="mobile">Mobile : 0428 351 972</li>
      <li class="postal">PO Box 847, Brellin VR 6971</li>
      <li class="abn">ABN 52 714 309 268</li>
      <li class="licence">Lic 7164/2918</li>
      <li class="web">www.telvikbdr.com.au</li>
    </ul>

    <div class="vehicle-photo" role="img" aria-label="Photo of a white Korimu Daltra mini bus, front three-quarter view"></div>
  </div>
</body>
</html>
```